Halvor Grading and Septic needs a flyer to submit to contractors to offer our services

I need a sleek profession one page full color high gloss document showcasing our services to give to Mobile Home Companies and contractors that need our services.

Target Market(s)

Home Builders. Mobile Home Salesmen. People Building new homes.

Industry/Entity Type

Construction

Font styles to use
Serif
Sans Serif

Requirements
Must have
• Phone Number. Email address. Logo. Services offered: Mobile Home Pads, Meter Pole Placement and Connection, Waterline Connection, On Site Septic System Installs
Should not have
• Jokes, Nothing trying to be cute

```html
<!DOCTYPE html>
<html lang="en">
<head>
<meta charset="utf-8">
<title>Halvor Grading and Septic – Services Flyer</title>
<link href="https://fonts.googleapis.com/css2?family=Poppins:ital,wght@0,500;0,600;0,700;0,800;1,600;1,700;1,800;1,900&family=Montserrat:wght@500;600;700&display=swap" rel="stylesheet">
<style>
  :root {
    --navy: #174f86;
    --red: #cf2128;
    --white: #ffffff;
    --ring: #8fb0d3;
    --sky-top: #4f8ccf;
    --sky-low: #a9c9ea;
    --field: #6f8b52;
    --dirt: #b5744a;
    --map-land: #eef1e4;
    --map-green: #d8e8cf;
    --map-road: #f2d98a;
  }
  * { box-sizing: border-box; margin: 0; padding: 0; }
  html, body { width: 803px; height: 1200px; overflow: hidden; background: #666; }
  .flyer {
    position: relative; width: 803px; height: 1200px; overflow: hidden;
    background: var(--navy); color: var(--white);
    font-family: "Poppins", sans-serif;
  }
  .flyer__frame { position: absolute; inset: 0; }
  .brand {
    position: absolute; left: 44px; top: 44px; width: 240px;
    color: var(--navy); font-weight: 800;
    font-size: 27px; line-height: 1.08; text-transform: uppercase; text-align: center;
  }
  .headline {
    position: absolute; left: 0; right: 0; top: 490px; text-align: center;
    font-style: italic; font-weight: 900; font-size: 43px; line-height: 40px;
    text-transform: uppercase; letter-spacing: 0.3px;
  }
  .intro {
    position: absolute; left: 0; right: 0; top: 590px; text-align: center;
    font-style: italic; font-weight: 600; font-size: 15px; line-height: 18px;
  }
  .intro__cta {
    display: block; margin-top: 3px; font-weight: 800; font-size: 21px; line-height: 24px;
  }
  .section-title {
    position: absolute; font-style: italic; font-weight: 800; font-size: 28px; line-height: 32px;
  }
  .section-title--services { left: 70px; top: 682px; }
  .section-title--area { left: 499px; top: 684px; }
  .services { position: absolute; left: 67px; top: 733px; width: 360px; list-style: none; }
  .service { position: relative; height: 92px; display: flex; align-items: center; }
  .service__icon {
    width: 82px; height: 82px; border-radius: 50%; flex: none;
    background: var(--red); border: 6px solid var(--ring);
    display: flex; align-items: center; justify-content: center;
  }
  .service__label {
    margin-left: 12px; font-family: "Montserrat", sans-serif; font-weight: 700;
    font-size: 17.5px; line-height: 22px; text-transform: uppercase;
  }
  .service + .service::before {
    content: ""; position: absolute; left: 94px; right: 12px; top: 0;
    border-top: 1px solid rgba(255,255,255,0.55);
  }
  .map {
    position: absolute; left: 466px; top: 731px; width: 285px; height: 255px;
    border-radius: 8px; border: 4px solid var(--white);
    background: linear-gradient(135deg, var(--map-land) 0%, var(--map-green) 45%, var(--map-land) 70%, var(--map-road) 100%);
  }
  .coverage {
    position: absolute; left: 471px; top: 1004px; width: 320px;
    display: grid; grid-template-columns: 153px 160px; row-gap: 4px;
    list-style: none; font-family: "Montserrat", sans-serif; font-weight: 500;
    font-size: 13px; line-height: 14px; text-transform: uppercase;
  }
  .coverage li { position: relative; padding-left: 18px; }
  .coverage li::before {
    content: ""; position: absolute; left: 0; top: 2px; width: 10px; height: 10px;
    border-radius: 50%; background: var(--white);
  }
  .contact { position: absolute; right: 40px; top: 1124px; text-align: right; font-style: italic; }
  .contact__phone {
    display: flex; align-items: center; justify-content: flex-end; gap: 10px;
    font-weight: 900; font-size: 34px; line-height: 40px;
  }
  .contact__email {
    display: flex; align-items: center; justify-content: flex-end; gap: 8px;
    font-weight: 600; font-size: 18px; line-height: 22px;
  }
</style>
</head>
<body>
<main class="flyer">
  <svg class="flyer__frame" width="803" height="1200" viewBox="0 0 803 1200" aria-hidden="true">
    <rect x="0" y="0" width="803" height="168" fill="var(--white)"/>
    <polygon points="358,28 803,28 803,172 0,172 0,160 330,160" fill="var(--navy)"/>
    <polygon points="0,335 706,335 656,468 82,468" fill="var(--red)" stroke="var(--white)" stroke-width="4"/>
    <line x1="0" y1="1192" x2="300" y2="1192" stroke="var(--white)" stroke-width="4"/>
    <polygon points="312,1108 803,1108 803,1200 284,1200" fill="var(--red)" stroke="var(--white)" stroke-width="4"/>
  </svg>
  <svg class="flyer__frame" width="803" height="1200" viewBox="0 0 803 1200" role="img" aria-label="Photo of a precast concrete septic tank being lowered by crane onto an excavated site">
    <defs>
      <linearGradient id="site-photo" x1="0" y1="0" x2="0" y2="1">
        <stop offset="0" stop-color="var(--sky-top)"/>
        <stop offset="0.62" stop-color="var(--sky-low)"/>
        <stop offset="0.8" stop-color="var(--field)"/>
        <stop offset="0.92" stop-color="var(--dirt)"/>
        <stop offset="1" stop-color="#9a5f3c"/>
      </linearGradient>
    </defs>
    <polygon points="392,58 803,58 803,335 666,335 626,429 119,429 107,335 0,335 0,164 365,164" fill="url(#site-photo)" stroke="var(--white)" stroke-width="5"/>
  </svg>

  <div class="brand">Halvor Grading<br>&amp; Septic</div>

  <h1 class="headline">Professional Wastewater<br>Management</h1>
  <p class="intro">Halvor Grading and Septic offers professional septic and<br>excavation services in East Texas.
    <span class="intro__cta">Call us now for a free estimate!</span></p>

  <h2 class="section-title section-title--services">Services offered:</h2>
  <ul class="services">
    <li class="service">
      <span class="service__icon">
        <svg width="44" height="44" viewBox="0 0 44 44" role="img" aria-label="Mobile home icon" fill="none" stroke="var(--white)" stroke-width="2.6" stroke-linejoin="round">
          <path d="M6 18 L22 8 L38 18"/><rect x="8" y="17" width="28" height="16"/>
          <rect x="12" y="21" width="7" height="6"/><rect x="24" y="21" width="8" height="12"/>
          <circle cx="13" cy="37" r="3"/><circle cx="21" cy="37" r="3"/>
        </svg>
      </span>
      <span class="service__label">Mobile Home Pads</span>
    </li>
    <li class="service">
      <span class="service__icon">
        <svg width="44" height="44" viewBox="0 0 44 44" role="img" aria-label="Meter pole icon" fill="none" stroke="var(--white)" stroke-width="2.6" stroke-linecap="round">
          <path d="M14 6 V38"/><path d="M6 10 H22"/><path d="M8 14 H20"/>
          <rect x="24" y="22" width="14" height="14" rx="2"/><path d="M27 27 H35 M27 31 H35"/>
          <path d="M14 24 H24"/>
        </svg>
      </span>
      <span class="service__label">Meter Pole Placement<br>and Connection</span>
    </li>
    <li class="service">
      <span class="service__icon">
        <svg width="44" height="44" viewBox="0 0 44 44" role="img" aria-label="Waterline icon" fill="none" stroke="var(--white)" stroke-width="3" stroke-linejoin="round">
          <path d="M6 14 H22 V32 H38"/><path d="M6 10 V18"/><path d="M38 28 V36"/>
          <path d="M30 6 V14 H22"/><path d="M26 6 H34"/>
        </svg>
      </span>
      <span class="service__label">Waterline Connection</span>
    </li>
    <li class="service">
      <span class="service__icon">
        <svg width="44" height="44" viewBox="0 0 44 44" role="img" aria-label="Septic tank icon" fill="var(--white)">
          <rect x="6" y="18" width="32" height="18" rx="3"/>
          <rect x="11" y="9" width="8" height="10"/><rect x="25" y="9" width="8" height="10"/>
          <rect x="9" y="7" width="12" height="3"/><rect x="23" y="7" width="12" height="3"/>
        </svg>
      </span>
      <span class="service__label">On Site Septic System<br>Installs</span>
    </li>
  </ul>

  <h2 class="section-title section-title--area">Service Area</h2>
  <div class="map" role="img" aria-label="Map of East Texas with a circle marking the service radius"></div>
  <ul class="coverage">
    <li>Pads</li>
    <li>Septic Systems</li>
    <li>Meter Pole and Electric</li>
    <li>Septic Design and Site Evaluation</li>
    <li>Water Lines</li>
  </ul>

  <div class="contact">
    <p class="contact__phone">
      <svg width="26" height="26" viewBox="0 0 24 24" aria-hidden="true"><path d="M6.6 10.8a15 15 0 0 0 6.6 6.6l2.2-2.2a1 1 0 0 1 1-.25 11.4 11.4 0 0 0 3.6.57 1 1 0 0 1 1 1V20a1 1 0 0 1-1 1A17 17 0 0 1 3 4a1 1 0 0 1 1-1h3.5a1 1 0 0 1 1 1c0 1.25.2 2.45.57 3.57a1 1 0 0 1-.25 1z" fill="var(--white)"/></svg>
      (903) 555-0147</p>
    <p class="contact__email">
      <svg width="20" height="20" viewBox="0 0 24 24" aria-hidden="true"><circle cx="12" cy="12" r="12" fill="var(--white)"/><rect x="6" y="8" width="12" height="8" fill="none" stroke="var(--red)" stroke-width="1.6"/><path d="M6 8l6 5 6-5" fill="none" stroke="var(--red)" stroke-width="1.6"/></svg>
      office@halvorgradingseptic.com</p>
  </div>
</main>
</body>
</html>
```